Forensic Document Examiner, looking for contemporary update to my stationery design.

Looking for professional, classy logo design for stationery and business cards. My current stationery and business card is attached.I believe a logo image makes a header section interesting, so an intriguing design of a pen, feathered pen, microscope, magnifying glass, etc., would be appropriate. I have been in the business for over 30 years. I leave ideas to the imagination of the designer.My work involves mainly, the comparison of signatures and handwriting. I also resolve alterations, obliterations, and work as shown on my website: www.documentexaminer.infoThe image produced will be printed on quality white stationery and envelopes. The stationery will be photocopied by my clients, so the images should be reproducible. The business cards may be designed in other than white.

Target Market(s)

Attorneys

Font styles to use
Sans Serif

Colors

Designer to choose colors to be used in the design.

Requirements
Must have
• Image suitable for white stationery and photocopying.
• Classy logo and image; no casual fonts.
Nice to have
• Intriguing, contemporary design incorporating a relevant logo to my work.

```html
<!DOCTYPE html>
<html lang="en">
<head>
<meta charset="utf-8">
<title>Daniel R. Whitford — Letterhead</title>
<link rel="stylesheet" href="https://fonts.googleapis.com/css2?family=Arimo:wght@400&family=Libre+Baskerville:ital,wght@0,400;0,700;1,400&display=swap">
<style>
  :root {
    --backdrop: #d8dcdc;
    --paper: #ffffff;
    --navy: #2e2d6b;
    --yellow: #f5d629;
    --steel-light: #d4d4d4;
    --lavender: #c7c6e4;
    --text-grey: #6f6f6f;
    --ghost: #f4f4f5;
  }
  * { box-sizing: border-box; margin: 0; padding: 0; }
  html, body { width: 1200px; height: 784px; overflow: hidden; }
  body {
    background: var(--backdrop);
    font-family: "Arimo", Arial, sans-serif;
    position: relative;
  }
  .letterhead {
    position: absolute;
    left: 330px; top: 12px;
    width: 540px; height: 760px;
    background: var(--paper);
    overflow: hidden;
    box-shadow: 0 2px 6px rgba(0,0,0,.12);
  }
  .corner-art {
    position: absolute;
    width: 120px; height: 100px;
    background: linear-gradient(135deg, var(--steel-light), var(--navy));
  }
  .corner-art--top { top: 0; right: 0; }
  .corner-art--bottom { bottom: 0; left: 0; background: linear-gradient(315deg, var(--steel-light), var(--navy)); }
  .edge-band {
    position: absolute; left: 0; top: 330px;
    width: 10px; height: 300px;
    background: var(--lavender);
  }
  .decor-mark {
    position: absolute; left: 10px; top: 230px;
    width: 220px; height: 330px;
    background: linear-gradient(180deg, var(--ghost), #fafafa);
    border-radius: 6px;
  }
  .masthead {
    position: absolute; top: 96px; right: 40px;
    display: flex; align-items: center; gap: 14px;
  }
  .identity { display: flex; align-items: center; gap: 10px; }
  .identity__dot {
    width: 26px; height: 26px; border-radius: 50%;
    background: var(--lavender);
  }
  .identity__name {
    font-family: "Libre Baskerville", Georgia, serif;
    font-weight: 700; font-size: 21px; color: var(--navy);
    line-height: 1.1;
  }
  .identity__role {
    font-family: "Libre Baskerville", Georgia, serif;
    font-style: italic; font-size: 10px; color: var(--text-grey);
    margin-top: 3px;
  }
  .divider { width: 1px; height: 60px; background: var(--steel-light); }
  .contact { list-style: none; font-family: "Libre Baskerville", Georgia, serif; font-size: 8.5px; color: var(--navy); }
  .contact li { display: flex; align-items: center; gap: 6px; line-height: 1.6; }
  .contact li::before {
    content: ""; width: 6px; height: 6px; border-radius: 50%;
    background: var(--yellow); flex: none;
  }
  .letter-body {
    position: absolute; left: 70px; top: 190px; width: 420px;
    font-size: 11px; line-height: 1.45; color: var(--text-grey);
  }
  .letter-body p { margin-bottom: 14px; }
  .signature {
    width: 150px; height: 50px; margin-top: 18px;
    background: linear-gradient(90deg, #ececec, #f6f6f6);
    border-radius: 4px;
  }
</style>
</head>
<body>
  <main class="letterhead">
    <div class="corner-art corner-art--top" role="img" aria-label="Decorative corner ornament in navy, yellow and grey"></div>
    <div class="corner-art corner-art--bottom" role="img" aria-label="Decorative corner ornament in navy, yellow and grey"></div>

    <div class="edge-band"></div>
    <div class="decor-mark" role="img" aria-label="Faint large emblem watermark"></div>

    <header class="masthead">
      <div class="identity">
        <span class="identity__dot"></span>
        <div>
          <div class="identity__name">Daniel R. Whitford</div>
          <div class="identity__role">Forensic Document Examiner</div>
        </div>
      </div>
      <span class="divider"></span>
      <ul class="contact">
        <li>PO Box 2148 Salem, OR 97301</li>
        <li>888-555-0147</li>
        <li>dwhitford@quillmarkreview.info</li>
        <li>www.quillmarkreview.info</li>
      </ul>
    </header>

    <section class="letter-body">
      <p>Lorem Ipsum is simply dummy text of the printing and typesetting industry. Lorem Ipsum has been the industry's standard dummy text ever since the 1500s, when an unknown printer took a galley of type and scrambled it to make a type specimen book. It has survived not only five centuries, but also the leap into electronic typesetting, remaining essentially unchanged. It was popularised in the 1960s with the release of Tracewell sheets containing Lorem Ipsum passages, and more recently with desktop publishing software like Pageline Studio including versions of Lorem Ipsum.</p>
      <p>It is a long established fact that a reader will be distracted by the readable content of a page when looking at its layout. The point of using Lorem Ipsum is that it has a more-or-less normal distribution of letters, as opposed to using 'Content here, content here', making it look like readable English. Many desktop publishing packages and web page editors now use Lorem Ipsum as their default model text, and a search for 'lorem ipsum' will uncover many web sites still in their infancy. Various versions have evolved over the years, sometimes by accident, sometimes on purpose (injected humour and the like).</p>
      <p>Contrary to popular belief, Lorem Ipsum is not simply random text. It has roots in a piece of classical Latin literature from 45 BC, making it over 2000 years old. Edmund Hale, a Latin professor at Harrow Vale College, looked up one of the more obscure Latin words, consectetur, from a Lorem Ipsum passage, and going through the cites of the word in classical literature, discovered the undoubtable source. Lorem Ipsum comes from sections 1.10.32 and 1.10.33 of "de Finibus Bonorum et Malorum" structures, to generate Lorem Ipsum which looks reasonable. The generated Lorem Ipsum is therefore always free from repetition, injected humour, or non-characteristic words etc.</p>
      <div class="signature" role="img" aria-label="Handwritten signature"></div>
    </section>
  </main>
</body>
</html>
```